Business Recognition Design

We need a design for a recognition to be given to business leaders in our community.
The recognition shall be made on a brass plaque on wood panel background (picture attached, please use it as a background), and all drawing must be in vectors and only one color (black).
It should also have a logo on the top and signature on the right bottom.
The text is enclosed in DOC file.
Updates

Reason: just to be able to find the best solution

Reason: None of the suggestion is good enough. Logo in general is too big in comparison with the rest of the plate.

Industry/Entity Type

Business

Requirements
Must have
• - standard Windows font (or possibility to install the same font on Windows), as the name on the recognition shall be printed in the same font
Nice to have
• - some graphic element (in curves) representing achievements in business
- should look great :)

```html
<!DOCTYPE html>
<html lang="de">
<head>
<meta charset="utf-8">
<title>Auszeichnung – Unternehmer Deutschlands 2013</title>
<link rel="stylesheet" href="https://fonts.googleapis.com/css2?family=Tinos:wght@400;700&display=swap">
<style>
  :root {
    --backdrop: #3b3b3b;
    --wood-dark: #4a2c18;
    --wood-mid: #6b4226;
    --wood-light: #7d5030;
    --brass-light: #f3e07a;
    --brass-mid: #dcbf3c;
    --brass-deep: #b8951f;
    --brass-edge: #8f7218;
    --screw: #c9a83a;
    --ink: #111111;
    --art-dark: #3a2e10;
  }
  html, body {
    margin: 0;
    padding: 0;
    width: 1200px;
    height: 832px;
    overflow: hidden;
    background: var(--backdrop);
  }
  .canvas {
    position: relative;
    width: 1200px;
    height: 832px;
    font-family: "Tinos", "Times New Roman", serif;
    color: var(--ink);
  }
  .wood-panel {
    position: absolute;
    left: 162px;
    top: 33px;
    width: 868px;
    height: 672px;
    background: linear-gradient(90deg, var(--wood-dark), var(--wood-light) 30%, var(--wood-mid) 60%, var(--wood-dark));
    border-radius: 3px;
  }
  .brass-plate {
    position: absolute;
    left: 187px;
    top: 57px;
    width: 818px;
    height: 626px;
    background: linear-gradient(160deg, var(--brass-light) 0%, var(--brass-mid) 40%, var(--brass-light) 65%, var(--brass-deep) 100%);
    box-shadow: inset 0 0 0 2px var(--brass-edge);
  }
  .screw {
    position: absolute;
    width: 20px;
    height: 20px;
    border-radius: 50%;
    background: radial-gradient(circle at 35% 35%, #fff3b0, var(--screw) 55%, var(--brass-edge));
  }
  .screw.tl { left: 218px; top: 83px; }
  .screw.tr { left: 962px; top: 83px; }
  .screw.bl { left: 218px; top: 628px; }
  .screw.br { left: 962px; top: 628px; }

  .line { position: absolute; left: 261px; margin: 0; white-space: nowrap; line-height: 1; }
  .brand-name { left: 263px; top: 156px; font-size: 40px; font-weight: 700; }
  .award-title { top: 214px; font-size: 44px; font-weight: 400; }
  .award-sub { top: 264px; font-size: 33px; font-weight: 700; }
  .award-sub.second { top: 303px; font-size: 33px; }
  .recipient-for { top: 343px; font-size: 23px; }
  .recipient-name { top: 369px; font-size: 29px; font-weight: 700; }
  .citation { font-size: 21px; }
  .citation.l1 { top: 409px; }
  .citation.l2 { top: 439px; }
  .citation.l3 { top: 469px; }
  .citation.l4 { top: 499px; }
  .citation strong { font-size: 22px; }
  .citation .small-name { font-size: 15px; font-weight: 700; }
  .signature-line { top: 603px; font-size: 23px; }

  .achievement-art {
    position: absolute;
    left: 660px;
    top: 222px;
    width: 292px;
    height: 393px;
  }
</style>
</head>
<body>
<div class="canvas">
  <div class="wood-panel"></div>
  <div class="brass-plate"></div>
  <span class="screw tl"></span>
  <span class="screw tr"></span>
  <span class="screw bl"></span>
  <span class="screw br"></span>

  <p class="line brand-name">KapitalWerk</p>

  <h1 class="line award-title">AUSZEICHNUNG</h1>
  <p class="line award-sub">als herausragendster</p>
  <p class="line award-sub second">Unternehmer Deutschlands 2013</p>
  <p class="line recipient-for">für</p>
  <p class="line recipient-name">Herrn Dipl.-Kfm. Max Muster</p>

  <p class="line citation l1">Unter der Leitung von <strong>Herr Dipl.-Kfm.</strong> <span class="small-name">Max Muster</span></p>
  <p class="line citation l2">hat sich die FIRMA GmbH im Jahr 2013 unter</p>
  <p class="line citation l3">den ersten 5% der größten deutschen</p>
  <p class="line citation l4">Wirtschaftsunternehmen platziert.</p>

  <p class="line signature-line">Gilching, 20. Juni 2013 Lena Hartwig</p>

  <svg class="achievement-art" role="img" aria-label="Grafik: aufsteigende Balken mit Stern über konzentrischen Zielringen als Symbol für geschäftlichen Erfolg" viewBox="0 0 292 393">
    <defs>
      <linearGradient id="artFill" x1="0" y1="0" x2="0" y2="1">
        <stop offset="0" stop-color="var(--brass-deep)" stop-opacity="0.35"/>
        <stop offset="1" stop-color="var(--art-dark)" stop-opacity="0.55"/>
      </linearGradient>
    </defs>
    <path d="M110 6 Q110 0 116 0 H226 Q232 0 232 6 V262 H286 Q292 262 292 268 V387 Q292 393 286 393 H6 Q0 393 0 387 V268 Q0 262 6 262 H110 Z" fill="url(#artFill)"/>
  </svg>
</div>
</body>
</html>
```